"Fight Back" banner ad design

We have sketched the design and have images to consider including. We are looking for something striking, FIGHT BACK! with a clenched fist image, then a fading images of variance.png and hi-bill.png in the background. Tag line "Fight your water bill with your own data" optionally include "Tally Mode" rivo3196 logo, KPMT Design, LLC based in San Diego CA. Pre-order now, visit https://www.fundbeacon.com/rivometer @rivo3196, info@rivo3196.com

"Fight your water bill with your own data"

```html
<!DOCTYPE html>
<html lang="en">
<head>
<meta charset="utf-8">
<title>Fight Back – Rivo3196</title>
<link rel="stylesheet" href="https://fonts.googleapis.com/css2?family=Quicksand:wght@500;700&family=Roboto:wght@700&display=swap">
<style>
  :root {
    --navy: #0f3868;
    --ink: #1b3a6a;
    --teal-dark: #1e5868;
    --teal-light: #86cadd;
    --grid: #111;
    --paper: #ffffff;
    --skin-1: #e8b48f;
    --skin-2: #c98662;
    --bill-fade: #e3eaee;
  }
  html, body { margin: 0; padding: 0; overflow: hidden; background: var(--paper); }
  .banner {
    position: relative;
    width: 1200px;
    height: 662px;
    overflow: hidden;
    background: var(--paper);
    font-family: "Quicksand", sans-serif;
  }
  .bill-backdrop {
    position: absolute;
    left: 268px; top: 16px; width: 456px; height: 646px;
    background: linear-gradient(180deg, #cfdde4 0 4%, var(--bill-fade) 4% 100%);
    opacity: .7;
  }
  .bill-strip {
    position: absolute;
    left: 0; top: 140px; width: 720px; height: 164px;
    background: linear-gradient(90deg, #8fcbe0 0 5%, #fdfdfd 5% 92%, #2b6170 92% 100%);
    transform: skewY(-3deg);
  }
  .fist-photo {
    position: absolute;
    left: 184px; top: 80px; width: 392px; height: 582px;
    border-radius: 140px 150px 40px 40px;
    background: radial-gradient(ellipse at 45% 35%, var(--skin-1), var(--skin-2));
  }
  .strip-name {
    position: absolute;
    left: 80px; top: 270px;
    margin: 0;
    font-size: 22px; font-weight: 700;
    color: #4d7c88;
    letter-spacing: .5px;
  }
  .headline {
    position: absolute;
    right: 18px; top: 2px;
    margin: 0;
    font-size: 118px; font-weight: 700;
    line-height: 1;
    color: var(--navy);
    letter-spacing: -1px;
  }
  .tagline {
    position: absolute;
    right: 22px; top: 140px;
    margin: 0;
    font-size: 43px; font-weight: 700;
    line-height: 56px;
    color: var(--navy);
    text-align: left;
  }
  .contact {
    position: absolute;
    left: 12px; top: 516px;
    margin: 0;
    font-size: 25px; font-weight: 700;
    line-height: 34px;
    color: var(--ink);
    text-shadow: 0 0 4px #fff, 0 0 8px #fff;
  }
  .usage-chart {
    position: absolute;
    left: 588px; top: 280px;
    width: 610px; height: 370px;
  }
  .usage-chart text { font-family: "Roboto", sans-serif; font-weight: 700; }
</style>
</head>
<body>
<main class="banner">
  <div class="bill-backdrop" role="img" aria-label="Faded water bill fees and charges statement in the background"></div>
  <div class="bill-strip" role="img" aria-label="Curled water bill strip showing fees and total due"></div>
  <div class="fist-photo" role="img" aria-label="Photo of a clenched fist gripping a water bill"></div>
  <p class="strip-name">Rivo3196</p>

  <h1 class="headline">FIGHT BACK!</h1>
  <p class="tagline">Fight your water bill<br>with your own data.</p>

  <p class="contact">
    LLC based in San Diego CA.<br>
    Pre-order now,<br>
    visit https://www.fundbeacon.com<br>
    rivometer @rivo3196, info@rivo3196.com
  </p>

  <svg class="usage-chart" viewBox="588 280 610 370" aria-label="Water use in HCF chart, previous year versus current year">
    <rect x="589" y="281" width="608" height="368" fill="#fff" stroke="var(--teal-dark)" stroke-width="2"/>
    <rect x="589" y="281" width="608" height="28" fill="var(--teal-dark)"/>
    <text x="893" y="302" fill="#fff" font-size="20" text-anchor="middle">WATER USE IN HCF (Hundred Cubic Feet)</text>

    <rect x="746" y="315" width="16" height="16" fill="var(--teal-light)" stroke="#555" stroke-width=".5"/>
    <text x="778" y="329" font-size="14" fill="#111">Previous Year</text>
    <rect x="904" y="315" width="16" height="16" fill="var(--teal-dark)"/>
    <text x="934" y="329" font-size="14" fill="#111">Current Year</text>

    <g class="grid" stroke="var(--grid)" stroke-width="1.2">
      <line x1="624" x2="1184" y1="646" y2="646"/><line x1="624" x2="1184" y1="626.8" y2="626.8"/>
      <line x1="624" x2="1184" y1="607.6" y2="607.6"/><line x1="624" x2="1184" y1="588.4" y2="588.4"/>
      <line x1="624" x2="1184" y1="569.2" y2="569.2"/><line x1="624" x2="1184" y1="550" y2="550"/>
      <line x1="624" x2="1184" y1="530.8" y2="530.8"/><line x1="624" x2="1184" y1="511.6" y2="511.6"/>
      <line x1="624" x2="1184" y1="492.4" y2="492.4"/><line x1="624" x2="1184" y1="473.2" y2="473.2"/>
      <line x1="624" x2="1184" y1="454" y2="454"/><line x1="624" x2="1184" y1="434.8" y2="434.8"/>
      <line x1="624" x2="1184" y1="415.6" y2="415.6"/><line x1="624" x2="1184" y1="396.4" y2="396.4"/>
      <line x1="624" x2="1184" y1="377.2" y2="377.2"/><line x1="624" x2="1184" y1="358" y2="358"/>
      <line x1="624" x2="1184" y1="338.8" y2="338.8"/>
    </g>
    <g class="axis-labels" font-size="12" fill="#111" text-anchor="end">
      <text x="618" y="650">0</text><text x="618" y="631">5</text><text x="618" y="612">10</text>
      <text x="618" y="592">15</text><text x="618" y="573">20</text><text x="618" y="554">25</text>
      <text x="618" y="535">30</text><text x="618" y="516">35</text><text x="618" y="496">40</text>
      <text x="618" y="477">45</text><text x="618" y="458">50</text><text x="618" y="439">55</text>
      <text x="618" y="420">60</text><text x="618" y="400">65</text><text x="618" y="381">70</text>
      <text x="618" y="362">75</text><text x="618" y="343">80</text>
    </g>
    <g class="bars-previous" fill="var(--teal-light)" stroke="#333" stroke-width=".6">
      <rect x="670" y="542.3" width="19" height="103.7"/>
      <rect x="764" y="515.4" width="19" height="130.6"/>
      <rect x="858" y="575" width="19" height="71"/>
      <rect x="952" y="532.7" width="19" height="113.3"/>
      <rect x="1047" y="550" width="19" height="96"/>
      <rect x="1141" y="550" width="19" height="96"/>
    </g>
    <g class="bars-current" fill="var(--teal-dark)" stroke="#222" stroke-width=".6">
      <rect x="694" y="557.7" width="19" height="88.3"/>
      <rect x="788" y="569.2" width="19" height="76.8"/>
      <rect x="882" y="569.2" width="19" height="76.8"/>
      <rect x="976" y="342.6" width="19" height="303.4"/>
      <rect x="1071" y="384.9" width="19" height="261.1"/>
      <rect x="1165" y="365.7" width="19" height="280.3"/>
    </g>
  </svg>
</main>
</body>
</html>
```